Need Business Card for our Real Estate Business with Sales Executive's Picture

PANTONE 484 C ( RED)

PANTONE 2766 C ( BLUE

Industry/Entity Type

Real Estate

Contact Information for Business Card

Name, Mobile, email, & picture of Person
Agency Phone, address, Web address

Requirements
Must have
• Our Logo Colours, Agent Picture,

```html
<!DOCTYPE html>
<html lang="en">
<head>
<meta charset="utf-8">
<title>Dunmore Real Estate — Business Cards</title>
<link href="https://fonts.googleapis.com/css2?family=Cinzel:wght@400;600&family=Crimson+Text:wght@400;600&display=swap" rel="stylesheet">
<style>
  :root {
    --navy: #141b4d;
    --red: #8a1c22;
    --white: #ffffff;
    --paper: #fbfbfb;
    --stage: #2a2a2c;
    --photo-a: #dfe3ec;
    --photo-b: #2f4aa0;
  }
  * { box-sizing: border-box; margin: 0; padding: 0; }
  html, body { width: 1200px; height: 880px; overflow: hidden; }
  body { background: var(--stage); position: relative; font-family: "Crimson Text", serif; }

  .card {
    position: absolute;
    width: 640px; height: 366px;
    background: var(--paper);
    border-radius: 26px;
    overflow: hidden;
    box-shadow: 0 12px 30px rgba(0,0,0,.45);
  }
  .card--back { left: 150px; top: 50px; }
  .card--front { left: 410px; top: 464px; }

  /* Brand lockup */
  .brand { position: absolute; color: var(--navy); font-family: "Cinzel", serif; font-weight: 600; z-index: 3; }
  .brand__row { display: flex; align-items: center; gap: 12px; }
  .brand__mark { width: 12px; height: 12px; background: var(--red); }
  .brand__name { font-size: 44px; letter-spacing: 4px; line-height: 1; }
  .brand__rule { height: 2px; background: var(--navy); margin: 8px 0 6px; }
  .brand__sub { font-size: 13px; letter-spacing: 3px; text-align: right; }

  .card--back .brand { left: 50%; top: 120px; transform: translateX(-50%); width: 330px; }
  .web { position: absolute; left: 0; right: 0; top: 262px; text-align: center;
         font-family: "Cinzel", serif; font-size: 15px; letter-spacing: 3px; color: var(--navy); }

  .card--front .brand { left: 56px; top: 44px; width: 290px; }
  .card--front .brand__name { font-size: 38px; }

  .photo {
    position: absolute; right: 0; top: 22px; width: 250px; height: 170px; z-index: 1;
    background: linear-gradient(180deg, var(--photo-a) 0%, var(--photo-b) 75%);
  }
  .wave { position: absolute; left: 0; top: 0; width: 640px; height: 366px; z-index: 2; }

  .contact { position: absolute; color: var(--white); z-index: 3; white-space: nowrap; }
  .contact__name { left: 62px; top: 264px; font-family: "Cinzel", serif; font-size: 19px; letter-spacing: 1px; line-height: 24px; }
  .contact__role { color: #c24a50; font-family: "Crimson Text", serif; font-size: 16px; margin-left: 4px; letter-spacing: 0; }
  .contact__addr { left: 84px; top: 292px; font-size: 16px; line-height: 19px; }
  .contact__line { display: flex; align-items: center; gap: 7px; font-size: 16px; line-height: 19px; }
  .contact__phone { left: 84px; top: 333px; }
  .contact__email { left: 340px; top: 292px; }
  .icon { width: 15px; height: 15px; border-radius: 50%; background: var(--red); display: inline-flex; align-items: center; justify-content: center; }
</style>
</head>
<body>

<section class="card card--back">
  <div class="brand">
    <div class="brand__row"><span class="brand__mark"></span><span class="brand__name">DUNMORE</span></div>
    <div class="brand__rule"></div>
    <div class="brand__sub">REAL ESTATE</div>
  </div>
  <p class="web">www.dunmorehomes.com</p>
</section>

<section class="card card--front">
  <div class="photo" role="img" aria-label="Portrait photo of the sales agent in a blue suit"></div>

  <svg class="wave" viewBox="0 0 640 366" aria-hidden="true">
    <path d="M0,196 C20,238 70,258 140,256 C260,250 340,200 420,182 C500,166 570,168 640,172 L640,366 L0,366 Z" fill="var(--navy)"/>
    <path d="M140,248 C260,242 340,190 420,171 C500,154 570,156 640,160" fill="none" stroke="var(--red)" stroke-width="5"/>
    <path d="M150,251 C265,245 342,195 422,177 C502,160 572,162 640,166" fill="none" stroke="var(--white)" stroke-width="1.5"/>
  </svg>

  <div class="brand">
    <div class="brand__row"><span class="brand__mark"></span><span class="brand__name">DUNMORE</span></div>
    <div class="brand__rule"></div>
    <div class="brand__sub">REAL ESTATE</div>
  </div>

  <p class="contact contact__name">LIAM CARTER <span class="contact__role">| Owner</span></p>
  <p class="contact contact__addr">PO Box 45 Harbour Lane<br>4th street Eastvale</p>
  <p class="contact contact__line contact__phone">
    <span class="icon"><svg width="7" height="10" viewBox="0 0 7 10"><rect x="0.5" y="0.5" width="6" height="9" rx="1.2" fill="none" stroke="#fff"/></svg></span>
    (555) 210-3344
  </p>
  <p class="contact contact__line contact__email">
    <span class="icon"><svg width="9" height="7" viewBox="0 0 9 7"><rect x="0.5" y="0.5" width="8" height="6" fill="none" stroke="#fff"/><path d="M0.5,0.5 L4.5,4 L8.5,0.5" fill="none" stroke="#fff"/></svg></span>
    hello@dunmorehomes.com
  </p>
</section>

</body>
</html>
```